Logo and Website Design for QR.KA Horizon - a Software Engineering and IT company

Software engineering and IT are two different disciplines - and yet inseparably linked. At QR.KA Horizon, we combine both worlds and ensure that our software solutions are not only innovative and powerful, but also integrate perfectly into existing IT landscapes. Vision stands more for imagination, so it is not neccessary something what has to do with visualisation. Please consider that the winning competitor is also instructed to make a logo for the company. So please make a suitable logo for QR.KA Horizon to which the website fits to and show it during the website creation process. A good Logo desing is important for winning the competition. The website should contain a landing page with inspiring, perhaps futuristic photos of a datacenter and lines of code. Eventuelly flewent integrated in the text. On the landing page the company should introduced with a small text (max 250 words) followed by a section with a short text to one of our products nearby a graphic visualising the architecture of the product. The menue should be on top and fixed during scrolling and consist of the menue items home, solutions, who are we and a contact button. There should be a footer for linking social media, rights and Impressum. Only as an idea not a must. The very first view on the landing page could also be the menue bar and below of it a transparent unsharp photo (e.g. datacenter, lines of code, both ;) with the company name in the center.

###############################################################

Hi Designers,

Despite your very good approaches for describing QR.KA Horizon, here a short introduction (german text) from ourself:

------
QR.KA Horizon – Ihr Partner für ganzheitliche Softwarelösungen

Die QR.KA Horizon ist ein dynamisches Unternehmen, das sich nicht nur auf die Konzeption, das Design und die Entwicklung maßgeschneiderter Software spezialisiert hat, sondern auch deren reibungslosen Betrieb sicherstellt. Mit einem Team aus erfahrenen Softwarearchitekten und IT-Professionals verbinden wir modernste Softwareentwicklung mit tiefgehendem IT-Know-how – für Lösungen, die nachhaltig, leistungsstark und zukunftssicher sind.

Software Engineering trifft IT – Perfektion in Kombination
Software Engineering und IT sind zwei unterschiedliche Disziplinen – und doch untrennbar miteinander verbunden. Wir bei QR.KA Horizon vereinen beide Welten und sorgen dafür, dass unsere Softwarelösungen nicht nur innovativ und leistungsfähig sind, sondern sich auch perfekt in bestehende IT-Landschaften integrieren.

Expertise mit Fokus auf Healthcare & komplexe IT-Umgebungen
Unsere Experten bringen jahrzehntelange Erfahrung aus dem Healthcare-Sektor mit und unterstützen IT-Abteilungen großer Kliniken in der Entwicklung und Optimierung von Softwarelösungen. Von Anwendungssoftware bis hin zu Steuerungssystemen – unsere Softwareingenieure wissen genau, worauf es ankommt.

Ganzheitlicher Ansatz – über die Software hinaus
Wir entwickeln nicht nur Software, sondern übernehmen auch die Verantwortung für deren stabile und effiziente Betriebsumgebung. Egal, ob on-premises, in der Cloud oder als SaaS-Lösung – wir kümmern uns um den kompletten Lifecycle Ihrer Anwendung.

Ihre Vision – unsere Mission.
Ob Neuentwicklung einer SaaS-Anwendung oder die Migration bestehender Lösungen in eine moderne SaaS-Umgebung – mit QR.KA Horizon haben Sie einen starken Partner an Ihrer Seite.

Lassen Sie uns gemeinsam die Zukunft Ihrer Software gestalten!
--------------

Our first solution called "Clear Record Transfer Gateway" (CLURA)
-------------------
Teilen Sie Ihre Daten sicher – ohne Kompromisse!

Sie nutzen eine relationale Datenbank (Brightcask, Tabulon Hub, Vellumdb etc.) und möchten ausgewählte Daten mit Dritten teilen – sei es für ein Data Warehouse, Business Controller, Lieferanten oder Kunden? Doch dabei sollen Datensicherheit, Integrität und Verfügbarkeit Ihrer primären Lösung in keiner Weise gefährdet werden?

Mit unserer Lösung erhalten Sie genau das: Maximalen Schutz für Ihre Anwendung bei gleichzeitigem Nutzen durch autorisierte Dritte – ganz ohne teure Lizenzkosten für eine Schattendatenbank.

Lassen Sie uns gemeinsam herausfinden, wie Sie Ihre Daten sicher und effizient nutzen können. Kontaktieren Sie uns – wir zeigen Ihnen, was möglich ist!
---------------------

Our second solution MIVO:
---------------------
MIVO – Program for a Tone Matching Instrument ist die smarte Lösung für Unternehmen, die bei Farbgenauigkeit keine Kompromisse machen. Die Software erkennt Farbabweichungen zwischen Mustern vollautomatisch, beschreibt sie verständlich und sorgt so für gleichbleibend hohe Produktqualität – schnell, visuell und präzise. Perfekt für alle, die Farbe zur Vertrauenssache machen.
-------------------------

Thanks,
Gerold

Target Market(s)

IT Professionals from any sector

Industry/Entity Type

Healthcare and other

Coding

Coded - Design and coding required

Number of Pages Required

1 page

Font styles to use
Sans Serif

Colors
0054AA
0677BA
7BADD7
CADEEF
E8F1F8
0094D4
00A9DD
6FCCEA
C7EBF8
E9F6FB
00AB8E
00BBA5
67D7C9
C6EFE9
E9F9F6

Requirements
Must have
• Please see description
Nice to have
• On the landing page the company should introduced with a small text (max 250 words) followed by a section with a short text to one of our products nearby a graphic visualising the architecture of the product. The menue should be on top and fixed during scrolling and consist of the menue items home, solutions, who are we and a contact button. There should be a footer for linking social media, rights and Impressum. Only as an idea not a must. The very first view on the landing page could also be the menue bar and below of it a transparent unsharp photo (e.g. datacenter, lines of code, both ;) with the company name in the center.
Should not have
• Please see description

```html
<!DOCTYPE html>
<html lang="de">
<head>
<meta charset="utf-8">
<title>QR.KA Horizon – Softwarelösungen</title>
<link href="https://fonts.googleapis.com/css2?family=Montserrat:wght@800&family=Source+Sans+3:wght@400;600;700&display=swap" rel="stylesheet">
<style>
:root{
  --blue-dark:#0054AA;
  --blue:#0677BA;
  --blue-pale:#E8F1F8;
  --teal:#00AB8E;
  --teal-mid:#00BBA5;
  --teal-light:#67D7C9;
  --ink:#111;
  --text:#2a2a2a;
  --navy:#020b1f;
  --white:#fff;
}
*{margin:0;padding:0;box-sizing:border-box}
html,body{width:1200px;height:3033px;overflow:hidden}
body{position:relative;background:var(--white);font-family:"Source Sans 3",sans-serif;color:var(--text)}
.abs{position:absolute}
.topbar{left:0;top:0;width:1200px;height:35px;background:var(--blue-pale);font-size:14px;color:#222}
.topbar .mail{left:141px;top:9px;display:flex;align-items:center;gap:8px}
.topbar .phone{right:141px;top:9px;display:flex;align-items:center;gap:8px}
.nav{left:0;top:35px;width:1200px;height:75px;background:var(--white);font-size:14px;color:#222}
.nav a{position:absolute;top:28px;text-decoration:none;color:#222}
.nav a.active{color:var(--teal)}
.logo{font-weight:700;color:var(--blue-dark);letter-spacing:-.3px}
.nav .logo{left:0;width:1200px;text-align:center;top:20px;font-size:32px}
.hero{left:0;top:110px}
.hero-title{left:0;top:296px;width:1200px;text-align:center;font-family:"Montserrat",sans-serif;font-weight:800;font-size:40px;line-height:51px;color:var(--white);text-shadow:0 2px 8px rgba(0,0,0,.5)}
.btn{display:inline-block;height:35px;line-height:35px;padding:0 15px;border-radius:18px;background:var(--teal);color:var(--white);font-size:14px;text-decoration:none}
.btn.blue{background:var(--blue-dark)}
.hero .btn,.hero-btn{left:523px;top:424px}
.ph{position:absolute}
.about-img{left:139px;top:767px;width:409px;height:411px;background:linear-gradient(160deg,#1b2a7a,#3a2a9e 45%,#a8326c 80%,#2a1b5a)}
.about-text{left:650px;top:830px;width:410px}
h2{font-weight:700;color:var(--ink);font-size:28px;line-height:36px}
.about-text h2 .brand{color:var(--blue-dark)}
p.body{font-size:13.5px;line-height:24px;margin-top:18px;letter-spacing:.2px}
.products{left:0;top:1178px;width:1200px;height:1165px;
  background:
   linear-gradient(var(--white),rgba(255,255,255,0) 90px,rgba(255,255,255,0) 1010px,var(--white)),
   repeating-linear-gradient(0deg,rgba(255,255,255,.55) 0 1px,transparent 1px 40px),
   repeating-linear-gradient(90deg,rgba(255,255,255,.55) 0 1px,transparent 1px 40px),
   var(--blue-pale)}
.products-head{left:0;top:1306px;width:1200px;text-align:center}
.products-head p{font-size:13.5px;line-height:19px;margin-top:12px;color:#222}
.product{width:410px}
.product h3{font-size:16.5px;font-weight:600;color:var(--ink);line-height:24px}
.product p{font-size:13.5px;line-height:23px;margin-top:14px}
.product .btn{margin-top:26px}
.p1{left:141px;top:1465px}
.p1-img{left:651px;top:1438px;width:409px;height:412px;background:radial-gradient(circle at 50% 50%,#4a38c8,#2c1a8a 55%,#27177e)}
.p2-img{left:145px;top:1889px;width:408px;height:412px;background:radial-gradient(circle at 50% 52%,#5a2fc2,#2f1888 55%,#27177e)}
.p2{left:650px;top:1915px}
.cta{left:0;top:2398px;width:1200px;height:400px;background:var(--teal-light)}
.cta h2{position:absolute;left:0;top:64px;width:1200px;text-align:center;font-size:27.5px;line-height:43px;color:#0a0f1c}
.cta .btn{position:absolute;left:522px;top:165px}
.footer{left:0;top:2640px}
.footer .logo{position:absolute;left:0;top:2805px;width:1200px;text-align:center;font-size:32px;color:var(--blue)}
.footer-mark{left:581px;top:2766px;width:38px;height:38px;border-radius:50%;border:3px solid var(--blue)}
.contact{top:2885px;display:flex;align-items:center;gap:12px;color:#e8eef6;font-size:13.5px;line-height:19px}
.sep{top:2880px;width:1px;height:40px;background:#1e2a44}
.bottombar{left:0;top:2982px;width:1200px;height:51px;background:var(--blue-dark);color:#e8eef6;font-size:13px}
.bottombar .copy{left:143px;top:17px}
.social{top:13px;width:26px;height:26px;border-radius:50%;border:1.5px solid rgba(255,255,255,.85)}
</style>
</head>
<body>

<div class="abs topbar">
  <div class="abs mail">
    <svg width="20" height="14" viewBox="0 0 20 14"><rect x="1" y="1" width="18" height="12" fill="none" stroke="#0054AA" stroke-width="2"/><path d="M1 1l9 7 9-7" fill="none" stroke="#0054AA" stroke-width="2"/></svg>
    info@qrkahorizon.example
  </div>
  <div class="abs phone">
    <svg width="18" height="18" viewBox="0 0 18 18"><path d="M4 2l3 3-2 2c1 2 3 4 5 5l2-2 3 3-2 2C8 15 3 10 2 4z" fill="none" stroke="#0054AA" stroke-width="1.6"/><path d="M11 2a5 5 0 0 1 5 5M11 5a2 2 0 0 1 2 2" fill="none" stroke="#0054AA" stroke-width="1.4"/></svg>
    +00 123 456 7890
  </div>
</div>

<nav class="abs nav">
  <a class="active" style="left:291px" href="#">Startseite</a>
  <a style="left:403px" href="#">Lösungen</a>
  <div class="abs logo">QR.KA Horizon</div>
  <a style="left:732px" href="#">Wer wir sind</a>
  <a style="left:862px" href="#">Kontakt</a>
</nav>

<svg class="abs hero" width="1200" height="572" viewBox="0 0 1200 572" role="img" aria-label="Unscharfes Foto eines Rechenzentrums mit leuchtenden Codezeilen">
  <defs>
    <linearGradient id="heroBg" x1="0" y1="0" x2="1" y2="0">
      <stop offset="0" stop-color="#1b2c44"/>
      <stop offset=".35" stop-color="#4a3424"/>
      <stop offset=".6" stop-color="#2a2a36"/>
      <stop offset="1" stop-color="#13304e"/>
    </linearGradient>
    <radialGradient id="glow" cx=".45" cy=".45" r=".5">
      <stop offset="0" stop-color="#c87a2a" stop-opacity=".55"/>
      <stop offset="1" stop-color="#c87a2a" stop-opacity="0"/>
    </radialGradient>
    <linearGradient id="arc" x1="0" y1="0" x2="1" y2="0">
      <stop offset="0" stop-color="#00BBA5"/>
      <stop offset=".5" stop-color="#67D7C9"/>
      <stop offset="1" stop-color="#0054AA"/>
    </linearGradient>
  </defs>
  <rect width="1200" height="572" fill="url(#heroBg)"/>
  <rect width="1200" height="572" fill="url(#glow)"/>
  <path d="M0 473 Q600 615 1200 473 L1200 572 L0 572 Z" fill="#fff"/>
  <path d="M141 512 Q600 610 1060 512 Q600 590 141 512 Z" fill="url(#arc)"/>
</svg>
<div class="abs hero-title">Technik im digitalen Zeitalter<br>Gestaltung von Lösungen durch Software</div>
<a class="abs btn hero-btn" href="#">Kontaktieren Sie uns</a>

<div class="ph about-img" role="img" aria-label="Foto eines Arbeitsplatzes mit Monitor und Tablet voller Programmcode"></div>
<div class="abs about-text">
  <h2><span class="brand">QR.KA Horizon</span>-Ihr Partner für ganzheitliche Softwarelösungen</h2>
  <p class="body">QR.KA Horizon ist ein dynamisches Unternehmen, das sich nicht nur auf die Konzeption, Gestaltung und Entwicklung von Individualsoftware spezialisiert hat, sondern auch für deren reibungslosen Betrieb sorgt. Mit einem Team aus erfahrenen Softwarearchitekten und IT-Profis verbinden wir modernste Softwareentwicklung mit fundiertem IT-Know-how - für Lösungen, die nachhaltig, leistungsstark und zukunftssicher sind.</p>
</div>

<div class="abs products"></div>
<div class="abs products-head">
  <h2>Ausgewähltes Produkt</h2>
  <p>Lorem ipsum dolor sit amet, consectetuer adipiscing elit, sed diam nonummy nibh euismod<br>tincidunt ut laoreet dolore magna aliquam erat volutpatt wisi enim ad minim veniam</p>
</div>

<div class="abs product p1">
  <h3>Offene Datenaustauschschnittstelle (CLURA)</h3>
  <p>Sie verwenden eine relationale Datenbank (Brightcask, Tabulon Hub, Vellumdb usw.) und möchten ausgewählte Daten mit Dritten teilen - sei es für ein Data Warehouse, Business Controller, Lieferanten oder Kunden? Sie wollen aber die Datensicherheit, -integrität und -verfügbarkeit Ihrer primären Lösung in keiner Weise gefährden? Mit unserer Lösung erhalten Sie genau das: maximalen Schutz für Ihre Anwendung bei gleichzeitiger Nutzung durch autorisierte Dritte - ohne die teuren Lizenzkosten für eine Schattendatenbank.<br>Lassen Sie uns gemeinsam herausfinden, wie Sie Ihre Daten sicher und effizient nutzen können.</p>
  <a class="btn" href="#">Kontaktieren Sie uns</a>
</div>
<div class="ph p1-img" role="img" aria-label="Illustration der Produktarchitektur: vernetzte Rechner um einen zentralen Datenknoten"></div>

<div class="ph p2-img" role="img" aria-label="Illustration einer Software-Analyse am Laptop mit Lupe"></div>
<div class="abs product p2">
  <h3>Software zur Qualitätssicherung der Farbgenauigkeit ( MIVO)</h3>
  <p>MIVO ist die intelligente Lösung für Unternehmen, die bei der Farbgenauigkeit keine Kompromisse eingehen. Die Software erkennt automatisch Farbabweichungen zwischen Mustern, beschreibt sie eindeutig und sorgt so für eine gleichbleibend hohe Produktqualität - schnell, visuell und präzise. Perfekt für alle, die Farbe zur Vertrauenssache machen.</p>
  <a class="btn" href="#">Kontaktieren Sie uns</a>
</div>

<section class="abs cta">
  <h2>Ermutigung der Besucher, sich mit Ihnen in Verbindung zu setzen, um<br>Lösungen für die sichere und effiziente Nutzung ihrer Daten zu finden.</h2>
  <a class="btn blue" href="#">Kontaktieren Sie uns</a>
</section>

<svg class="abs footer" width="1200" height="342" viewBox="0 0 1200 342">
  <path d="M141 78 Q600 -10 1060 78 Q600 10 141 78 Z" fill="#0054AA"/>
  <path d="M0 118 Q600 -30 1200 118 L1200 342 L0 342 Z" fill="#020b1f"/>
</svg>
<div class="abs footer-mark"></div>
<footer class="footer">
  <div class="logo">QR.KA Horizon</div>
</footer>
<div class="abs contact" style="left:255px">
  <svg width="32" height="32" viewBox="0 0 32 32"><path d="M16 3a8 8 0 0 1 8 8c0 6-8 14-8 14S8 17 8 11a8 8 0 0 1 8-8z" fill="none" stroke="#e8eef6" stroke-width="1.6"/><circle cx="16" cy="11" r="3" fill="none" stroke="#e8eef6" stroke-width="1.6"/><ellipse cx="16" cy="27" rx="12" ry="3" fill="none" stroke="#e8eef6" stroke-width="1.4"/></svg>
  <div>123, Building Name, Street<br>City, State XY 123456</div>
</div>
<div class="abs sep" style="left:502px"></div>
<div class="abs contact" style="left:545px">
  <svg width="32" height="32" viewBox="0 0 32 32"><path d="M6 5l6 6-3 3c2 4 5 7 9 9l3-3 6 6-4 4C13 28 4 19 2 9z" fill="none" stroke="#e8eef6" stroke-width="1.6"/><path d="M19 4a9 9 0 0 1 9 9M19 9a4 4 0 0 1 4 4" fill="none" stroke="#e8eef6" stroke-width="1.4"/></svg>
  <div>TELEFON<br>+00 123 456 7890</div>
</div>
<div class="abs sep" style="left:735px"></div>
<div class="abs contact" style="left:778px">
  <svg width="30" height="32" viewBox="0 0 30 32"><rect x="2" y="12" width="26" height="18" fill="none" stroke="#e8eef6" stroke-width="1.6"/><path d="M2 12l13 10 13-10M6 15V3h18v12M10 8h10M10 12h10" fill="none" stroke="#e8eef6" stroke-width="1.4"/></svg>
  <div>E-MAIL<br>info@qrkahorizon.example</div>
</div>

<div class="abs bottombar">
  <div class="abs copy">© 2025 QR.KA Horizon. All Rights Reserved.</div>
  <div class="abs social" style="left:928px"></div>
  <div class="abs social" style="left:963px"></div>
  <div class="abs social" style="left:998px"></div>
  <div class="abs social" style="left:1033px"></div>
</div>

</body>
</html>
```